Business Card for Fashion House

We need a business card design for our personalize fashion service for our customers. the business card should reflect reliability, luxury and creativity.
The brand Gravetto is extracted from "Graceful Velvetto"; Gravetto provides fashion designs sprinkled with luxury and style tailored for our elite clients character profile.
Gravetto is created for those who embody class and elegance with a passion for style.
Target Market(s)
Affluent Customers
Industry/Entity Type
Fashion
Contact Information for Business Card
Samira Haddadin
Fashion Designer
Telephone: +971 4 555 0192
Mobile +971 50 555 0147
Emal info@gravetto-example.com
Website www.gravetto-example.com
Social Media Youtube g+ Facebook Instagram Pin /gravetto
Font styles to use
Other font styles liked:
- Audrey provided
Look and feel
Each slider illustrates characteristics of the customer's brand and the style your logo design should communicate.

```html
<!DOCTYPE html>
<html lang="en">
<head>
<meta charset="utf-8">
<title>Gravetto – Business Card</title>
<link rel="stylesheet" href="https://fonts.googleapis.com/css2?family=Marcellus&family=Cormorant+Garamond:ital,wght@1,500&display=swap">
<style>
  :root {
    --stage: #1a1a1a;
    --card-black: #0b0b0b;
    --card-sheen: #2a2a2a;
    --panel-grey: #6e6e6e;
    --panel-grey-dark: #4a4a4a;
    --ink-white: #f2f2f2;
    --ink-soft: #cfcfcf;
    --shadow: rgba(0, 0, 0, 0.6);
  }
  * { box-sizing: border-box; margin: 0; padding: 0; }
  html, body {
    width: 1200px; height: 864px; overflow: hidden;
    background: var(--stage);
  }
  .stage {
    width: 1200px; height: 864px;
    display: flex; align-items: center; justify-content: center; gap: 20px;
  }
  .card {
    position: relative;
    width: 560px; height: 320px;
    background: linear-gradient(160deg, var(--card-sheen) 0%, var(--card-black) 45%, var(--card-black) 100%);
    box-shadow: 0 14px 30px var(--shadow);
    overflow: hidden;
    font-family: "Marcellus", serif;
    color: var(--ink-white);
  }
  .card__art { position: absolute; inset: 0; }

  .front__rule {
    position: absolute; left: 40px; right: 30px; top: 52px;
    height: 1px; background: var(--ink-white);
  }
  .front__person { position: absolute; right: 32px; top: 60px; text-align: right; }
  .front__name { font-size: 18px; letter-spacing: 1px; text-transform: uppercase; }
  .front__role {
    font-family: "Cormorant Garamond", serif; font-style: italic; font-weight: 500;
    font-size: 15px; color: var(--ink-soft); border-top: 1px solid var(--ink-white);
    padding-top: 1px; display: inline-block; margin-top: 1px;
  }
  .brand {
    position: absolute; left: 40px; top: 190px;
    display: flex; align-items: center; gap: 12px;
  }
  .brand__dot { width: 10px; height: 10px; border-radius: 50%; background: var(--ink-white); }
  .brand__name { font-size: 24px; letter-spacing: 7px; text-transform: uppercase; }

  .contacts {
    position: absolute; right: 24px; top: 196px;
    list-style: none; text-align: right; font-size: 13px; letter-spacing: 0.8px;
  }
  .contacts li { display: flex; align-items: center; justify-content: flex-end; gap: 8px; margin-bottom: 8px; }
  .contacts svg { width: 12px; height: 12px; flex: none; }

  .back__pattern { position: absolute; inset: 0; }
  .back__brand {
    position: absolute; right: 46px; top: 200px;
    font-size: 20px; letter-spacing: 6px; text-transform: uppercase;
  }
</style>
</head>
<body>
<main class="stage">

  <section class="card card--front" aria-label="Card front">
    <svg class="card__art" viewBox="0 0 560 320" aria-hidden="true">
      <defs>
        <linearGradient id="panelFill" x1="0" y1="0" x2="1" y2="1">
          <stop offset="0" stop-color="var(--panel-grey)"/>
          <stop offset="1" stop-color="var(--panel-grey-dark)"/>
        </linearGradient>
      </defs>
      <path d="M270 320 Q292 150 560 112 L560 320 Z" fill="url(#panelFill)"/>
      <path d="M270 320 Q292 150 560 112" fill="none" stroke="var(--ink-white)" stroke-width="7"/>
    </svg>

    <div class="front__rule"></div>
    <div class="front__person">
      <p class="front__name">Samira Haddadin</p>
      <p class="front__role">Fashion Designer</p>
    </div>

    <div class="brand">
      <span class="brand__dot"></span>
      <span class="brand__name">Gravetto</span>
    </div>

    <ul class="contacts">
      <li>+971 4 555 0192
        <svg viewBox="0 0 12 12"><circle cx="6" cy="6" r="5.2" fill="none" stroke="currentColor"/><path d="M3.5 7.5h5v-1l-1-1.5h-3l-1 1.5z" fill="currentColor"/></svg></li>
      <li>+971 50 555 0147
        <svg viewBox="0 0 12 12"><circle cx="6" cy="6" r="5.2" fill="none" stroke="currentColor"/><rect x="4.3" y="3" width="3.4" height="6" rx="0.6" fill="none" stroke="currentColor" stroke-width="0.9"/></svg></li>
      <li>info@gravetto-example.com
        <svg viewBox="0 0 12 12"><circle cx="6" cy="6" r="5.2" fill="none" stroke="currentColor"/><rect x="3.3" y="4" width="5.4" height="4" fill="none" stroke="currentColor" stroke-width="0.9"/><path d="M3.3 4l2.7 2 2.7-2" fill="none" stroke="currentColor" stroke-width="0.9"/></svg></li>
      <li>www.gravetto-example.com
        <svg viewBox="0 0 12 12"><circle cx="6" cy="6" r="5.2" fill="none" stroke="currentColor"/><circle cx="6" cy="6" r="3" fill="none" stroke="currentColor" stroke-width="0.8"/><path d="M3 6h6M6 3v6" stroke="currentColor" stroke-width="0.8"/></svg></li>
    </ul>
  </section>

  <section class="card card--back" aria-label="Card back">
    <svg class="back__pattern" viewBox="0 0 560 320" role="img" aria-label="Faint repeating brand pattern across the card back">
      <defs>
        <linearGradient id="patternTone" x1="0" y1="0" x2="1" y2="1">
          <stop offset="0" stop-color="#222"/>
          <stop offset="1" stop-color="#0e0e0e"/>
        </linearGradient>
      </defs>
      <rect width="560" height="320" fill="url(#patternTone)"/>
    </svg>
    <p class="back__brand">Gravetto</p>
  </section>

</main>
</body>
</html>
```